business card - for laser marking

I need design (curve) for my business card (make with laser) size 85mm x 55mm. How it look business card with laser marking see attached picture.

color:
Background: white
text and icons black

Please include: one side
1. dominik vrabec - direktor
2. phone: +386(0)41 726 190
+386(0)580 237 61
3. info@zarezko.example
4. faecebook.com/Zarezko.Ex
5. KM-ATELJE, Dominik Vrabec s.p.
Lipova ulica 19, 1000 Ljubljana, SI
6. logo

Please include: second side
1. logo
2. www.zarezko.example
3. Lasersko graviranje
ovitki telefonov, ohišja telefonov / tablic, nakit, ure, alu vizitke, dog-tagi, kemični svinčniki, orodja, noži, vžigalniki

Industry/Entity Type

Business

Contact Information for Business Card

Please include: one side
+386(0)580 237 61
3. info@zarezko.example
6. logo

1. logo
2. www.zarezko.example
3. Lasersko graviranje

Colors
000000
ffffff

Requirements
Must have
• I need design (curve) for my business card (make with laser) size 85mm x 55mm. How it look business card with laser marking see attached picture.
• color:
• Background: white
• text and icons black
• Please include: one side
• 1. dominik vrabec - direktor
• 2. phone: +386(0)41 726 190
• +386(0)580 237 61
• 3. info@zarezko.example
• 4. faecebook.com/Zarezko.Ex
• 5. KM-ATELJE, Dominik Vrabec s.p.
• Lipova ulica 19, 1000 Ljubljana, SI
• 6. logo
• Please include: second side
• 1. logo
• 2. www.zarezko.example
• 3. Lasersko graviranje
• ovitki telefonov, ohišja telefonov / tablic, nakit, ure, alu vizitke, dog-tagi, kemični svinčniki, orodja, noži, vžigalniki

```html
<!DOCTYPE html>
<html lang="sl">
<head>
<meta charset="utf-8">
<title>Zarezko – vizitka</title>
<link href="https://fonts.googleapis.com/css2?family=Roboto:wght@400;500&family=Roboto+Condensed:wght@700&display=swap" rel="stylesheet">
<style>
  :root {
    --backdrop: #5b4a3b;
    --card-white: #ffffff;
    --ink: #000000;
    --splash-tone: #d9d9d9;
  }
  html, body {
    margin: 0;
    width: 1200px;
    height: 960px;
    overflow: hidden;
    background: var(--backdrop);
    font-family: "Roboto", Arial, sans-serif;
  }
  .canvas { position: relative; width: 1200px; height: 960px; }
  .card {
    position: absolute;
    width: 602px;
    height: 344px;
    border-radius: 18px;
    overflow: hidden;
    background: var(--card-white);
    color: var(--ink);
  }
  .card--front { left: 318px; top: 102px; }
  .card--back { left: 319px; top: 493px; }

  .brand-mark {
    position: absolute;
    left: 0; right: 0; top: 138px;
    text-align: center;
    font-weight: 500;
    font-size: 26px;
    line-height: 32px;
    letter-spacing: 2px;
  }
  .brand-mark__dot {
    display: inline-block;
    width: 10px; height: 10px;
    border-radius: 50%;
    background: var(--ink);
    margin-left: 8px;
    vertical-align: middle;
  }
  .services {
    position: absolute;
    left: 0; right: 0; top: 246px;
    margin: 0;
    text-align: center;
    font-size: 15.3px;
    line-height: 18.5px;
  }
  .website {
    position: absolute;
    left: 0; right: 0; top: 306px;
    text-align: center;
    font-size: 17px;
    font-weight: 500;
  }

  .splash-area {
    position: absolute;
    left: 0; top: 0;
    width: 260px; height: 344px;
    background: linear-gradient(90deg, var(--splash-tone) 0%, rgba(217,217,217,0) 100%);
  }
  .person {
    position: absolute;
    right: 40px; top: 34px;
    text-align: right;
  }
  .person__name {
    font-family: "Roboto Condensed", "Arial Narrow", sans-serif;
    font-weight: 700;
    font-size: 22px;
    line-height: 26px;
    text-transform: uppercase;
  }
  .person__role { font-size: 14.5px; font-weight: 500; line-height: 20px; }
  .address {
    position: absolute;
    right: 40px; top: 158px;
    margin: 0;
    text-align: right;
    font-size: 14.5px;
    line-height: 18px;
    font-style: normal;
  }
  .contacts {
    position: absolute;
    right: 40px; top: 237px;
    margin: 0; padding: 0;
    list-style: none;
    text-align: right;
    font-size: 14.5px;
    line-height: 18.5px;
  }
  .contacts li { display: flex; justify-content: flex-end; align-items: center; gap: 7px; }
  .contacts svg { width: 14px; height: 14px; fill: var(--ink); }
  .contacts .square-icon { width: 13px; height: 13px; background: var(--ink); border-radius: 2px; }
</style>
</head>
<body>
<div class="canvas">
  <section class="card card--front">
    <div class="brand-mark">ZAREZKO<span class="brand-mark__dot"></span></div>
    <p class="services">
      Lasersko graviranje<br>
      ovitki telefonov, ohišja telefonov / tablic, nakit, ure, alu vizitke<br>
      dog-tagi, kemični svinčniki, orodja, noži, vžigalniki
    </p>
    <div class="website">www.zarezko.example</div>
  </section>

  <section class="card card--back">
    <div class="splash-area" role="img" aria-label="Paint splash decoration"></div>
    <div class="person">
      <div class="person__name">Dominik Vrabec</div>
      <div class="person__role">DIREKTOR</div>
    </div>
    <address class="address">
      KM-ATELJE<br>
      Dominik Vrabec s.p.<br>
      Lipova ulica 19<br>
      1000 Ljubljana, SI
    </address>
    <ul class="contacts">
      <li>+386(0)580 237 61
        <svg viewBox="0 0 24 24" aria-hidden="true"><path d="M6.6 10.8a15 15 0 0 0 6.6 6.6l2.2-2.2c.3-.3.7-.4 1-.2 1.1.4 2.3.6 3.6.6.6 0 1 .4 1 1V20c0 .6-.4 1-1 1A17 17 0 0 1 3 4c0-.6.4-1 1-1h3.5c.6 0 1 .4 1 1 0 1.3.2 2.5.6 3.6.1.3 0 .7-.2 1z"/></svg>
      </li>
      <li>+386(0)41 726 190
        <svg viewBox="0 0 24 24" aria-hidden="true"><path d="M7 1h10a2 2 0 0 1 2 2v18a2 2 0 0 1-2 2H7a2 2 0 0 1-2-2V3a2 2 0 0 1 2-2zm0 3v14h10V4zm5 15.5a1 1 0 1 0 0 2 1 1 0 0 0 0-2z"/></svg>
      </li>
      <li>info@zarezko.example
        <svg viewBox="0 0 24 24" aria-hidden="true"><path d="M2 5h20v2l-10 6L2 7zm0 4 10 6 10-6v10H2z"/></svg>
      </li>
      <li>Zarezko.Ex <span class="square-icon" aria-hidden="true"></span></li>
    </ul>
  </section>
</div>
</body>
</html>
```